Structural Engineering Business Card

Brookvane Drafting does residential house plans for clients in Central Florida. Would like simple but elegant business card that is appropriate for a house plan engineering company. Prefer black business card with black/white them but open to other shades of blue. I uploaded a sample card that I came across that looked good but please come up with your own creative designs.

Contact Information for Business Card

Name, Title, Phone, Email, Address, website

```html
<!DOCTYPE html>
<html lang="en">
<head>
<meta charset="utf-8">
<title>Brookvane Drafting – Business Card</title>
<link href="https://fonts.googleapis.com/css2?family=Poppins:wght@400;700&display=swap" rel="stylesheet">
<style>
  :root {
    --bg: #6b6b6b;
    --card-light: #ffffff;
    --card-dark: #000000;
    --ink: #111111;
    --ink-soft: #3a3a3a;
    --rule: #bdbdbd;
  }
  * { margin: 0; padding: 0; box-sizing: border-box; }
  html, body {
    width: 1093px; height: 1200px; overflow: hidden;
    background: var(--bg);
    font-family: "Poppins", sans-serif;
  }
  .canvas { position: relative; width: 1093px; height: 1200px; }

  .card { position: absolute; border-radius: 24px; overflow: hidden; }
  .card--front { left: 265px; top: 226px; width: 577px; height: 356px; background: var(--card-light); }
  .card--back  { left: 265px; top: 621px; width: 583px; height: 360px; background: var(--card-dark); }

  .brand {
    position: absolute;
    display: flex; align-items: center; gap: 8px;
    font-weight: 700; white-space: nowrap; text-transform: uppercase; letter-spacing: 0.5px;
  }
  .brand__mark { display: block; background: currentColor; }
  .card--front .brand { left: 22px; top: 168px; font-size: 20px; color: var(--ink); }
  .card--front .brand__mark { width: 14px; height: 14px; }
  .card--back .brand { left: 0; right: 0; top: 158px; justify-content: center; font-size: 36px; color: var(--card-light); gap: 14px; }
  .card--back .brand__mark { width: 26px; height: 26px; }

  .divider {
    position: absolute; left: 289px; top: 74px; width: 1px; height: 209px;
    background: linear-gradient(to bottom, transparent, var(--rule) 15%, var(--rule) 85%, transparent);
  }

  .details { position: absolute; left: 311px; top: 88px; color: var(--ink); }
  .details__name { font-weight: 700; font-size: 21px; line-height: 1.1; }
  .details__title { font-size: 16px; color: var(--ink-soft); line-height: 1.2; }
  .contact { list-style: none; margin-top: 14px; }
  .contact li { display: flex; align-items: center; gap: 7px; font-size: 16.5px; line-height: 21px; }
  .contact svg { width: 15px; height: 15px; flex: none; }
  .details__address { margin-top: 12px; font-size: 16.5px; line-height: 21px; font-style: normal; }
</style>
</head>
<body>
<div class="canvas">

  <section class="card card--front">
    <div class="brand"><span class="brand__mark"></span>Brookvane Drafting</div>
    <div class="divider"></div>
    <div class="details">
      <h1 class="details__name">DANIEL MERCER</h1>
      <p class="details__title">Managing Director</p>
      <ul class="contact">
        <li>
          <svg viewBox="0 0 24 24" aria-hidden="true"><path fill="currentColor" d="M6.6 10.8a15.1 15.1 0 0 0 6.6 6.6l2.2-2.2a1 1 0 0 1 1-.25 11.4 11.4 0 0 0 3.6.57 1 1 0 0 1 1 1V20a1 1 0 0 1-1 1A17 17 0 0 1 3 4a1 1 0 0 1 1-1h3.5a1 1 0 0 1 1 1c0 1.25.2 2.45.57 3.57a1 1 0 0 1-.25 1z"/></svg>
          044-555 218 730
        </li>
        <li>
          <svg viewBox="0 0 24 24" aria-hidden="true"><path fill="currentColor" d="M2 5h20v14H2z"/><path fill="none" stroke="#fff" stroke-width="1.6" d="M2.5 5.5 12 13l9.5-7.5M2.5 18.5l7-6.5m12 6.5-7-6.5"/></svg>
          hello@brookvane.com
        </li>
        <li>
          <svg viewBox="0 0 24 24" aria-hidden="true"><g fill="none" stroke="currentColor" stroke-width="1.8"><circle cx="12" cy="12" r="9.5"/><ellipse cx="12" cy="12" rx="4" ry="9.5"/><path d="M2.5 12h19M4 7h16M4 17h16"/></g></svg>
          www.brookvane.com
        </li>
      </ul>
      <address class="details__address">421, Address line goes here<br>45452,Country Name</address>
    </div>
  </section>

  <section class="card card--back">
    <div class="brand"><span class="brand__mark"></span>Brookvane Drafting</div>
  </section>

</div>
</body>
</html>
```